QVR business card

Need a business card for a company that provides instructional design and elearning development services. The website is here: http://quorvane.studio/

I'm attaching a current logo, as well as the old business card design. While I like to keep it clean, the old design is too simplistic for my liking. The only idea I want to reuse from the old design is placing industry jargon on the back of the card, just need a better way to present it. But if you have other ideas for the back--feel free to experiment.

Please use the colors complementary to the color we have on the website. Thank you!

```html
<!DOCTYPE html>
<html lang="en">
<head>
<meta charset="utf-8">
<title>QVR Business Card</title>
<link rel="stylesheet" href="https://fonts.googleapis.com/css2?family=Source+Sans+3:wght@400;600&display=swap">
<style>
  :root {
    --page-bg: #e8e8ea;
    --card-bg: #fafafa;
    --teal: #1bb3ad;
    --gold: #dccf92;
    --ink: #262626;
  }
  html, body {
    margin: 0;
    padding: 0;
    width: 1200px;
    height: 900px;
    overflow: hidden;
    background: var(--page-bg);
    font-family: "Source Sans 3", Arial, sans-serif;
  }
  .canvas {
    position: relative;
    width: 1200px;
    height: 900px;
  }
  .card {
    position: absolute;
    left: 150px;
    top: 172px;
    width: 900px;
    height: 556px;
    background: var(--card-bg);
    border-radius: 20px;
    overflow: hidden;
    box-shadow: 0 6px 24px rgba(0, 0, 0, 0.08);
  }
  .card__band {
    position: absolute;
    left: 0;
    right: 0;
  }
  .card__band--top {
    top: 0;
    height: 25px;
    background: var(--teal);
  }
  .card__band--bottom {
    bottom: 0;
    height: 27px;
    background: var(--gold);
  }
  .brand {
    position: absolute;
    left: 0;
    right: 0;
    top: 128px;
    display: flex;
    justify-content: center;
    align-items: center;
    gap: 18px;
  }
  .brand__mark {
    width: 64px;
    height: 64px;
  }
  .brand__name {
    font-size: 84px;
    font-weight: 600;
    line-height: 1;
    color: var(--gold);
    letter-spacing: 2px;
  }
  .holder {
    position: absolute;
    left: 0;
    right: 0;
    top: 330px;
    display: flex;
    align-items: center;
    gap: 14px;
  }
  .holder__rule {
    flex: 1;
    height: 2px;
    background: var(--teal);
  }
  .holder__name {
    font-size: 29px;
    font-weight: 600;
    color: var(--teal);
    white-space: nowrap;
  }
  .contact {
    position: absolute;
    left: 0;
    right: 0;
    top: 402px;
    margin: 0;
    text-align: center;
    font-size: 24px;
    line-height: 32px;
    color: var(--ink);
  }
  .contact__label {
    color: var(--teal);
    font-weight: 600;
  }
</style>
</head>
<body>
<div class="canvas">
  <div class="card">
    <div class="card__band card__band--top"></div>

    <div class="brand">
      <svg class="brand__mark" viewBox="0 0 64 64" aria-hidden="true">
        <circle cx="32" cy="32" r="30" fill="#1bb3ad"/>
      </svg>
      <span class="brand__name">QVR</span>
    </div>

    <div class="holder">
      <span class="holder__rule"></span>
      <span class="holder__name">Marek Telloway</span>
      <span class="holder__rule"></span>
    </div>

    <p class="contact">
      <span class="contact__label">Phone:</span> 555-014-2387<br>
      <span class="contact__label">Email:</span> mtelloway@quorvane.studio<br>
      <span class="contact__label">Website:</span> www.quorvane.studio
    </p>

    <div class="card__band card__band--bottom"></div>
  </div>
</div>
</body>
</html>
```